IT Staffing and Application Development

We need a facebook page for our IT Technology and Staffing company based in North America called Lanternfold Systems. We develop enterprise applications for respected fortune 500 companies. We also place top IT consultants to serve our clients needs. Please look at www.lanternfoldsystems.example for more details. The final design should communicate very high quality of our company, consultants and useful for marketing to new clients.
Updates

Target Market(s)

IT Directors, Managers, IT consultants, IT staffing

Industry/Entity Type

Marketing

Colors
acd036
3176b5
b768aa
f78f20

Requirements
Must have
• Please use the images and content in
www.lanternfoldsystems.example and should have all the content here
Nice to have
• Logo should indicated lanternfold capturing IT staffing, consulting and Application Development

```html
<!DOCTYPE html>
<html lang="en">
<head>
<meta charset="utf-8">
<title>Lanternfold Systems – Page Cover</title>
<link rel="stylesheet" href="https://fonts.googleapis.com/css2?family=Cormorant+SC:wght@500&family=Lato:wght@400&family=Alegreya+Sans+SC:wght@700&display=swap">
<style>
  :root {
    --lime: #acd036;
    --paper: #ececec;
    --white: #ffffff;
    --stage: #f4f5f7;
    --frame-grey: #b9bcc2;
  }
  * { margin: 0; padding: 0; box-sizing: border-box; }
  html, body { width: 1200px; height: 720px; overflow: hidden; }
  body { background: var(--stage); position: relative; font-family: "Lato", sans-serif; }

  .cover {
    position: absolute; left: 0; top: 100px; width: 1200px; height: 440px;
    background: var(--paper); overflow: hidden;
  }
  .cover__panel { position: absolute; inset: 0; }

  .headline {
    position: absolute; left: 32px; top: 42px;
    font-family: "Cormorant SC", serif; font-weight: 500;
    color: var(--lime); font-size: 38px; line-height: 56px; letter-spacing: 0.5px;
  }
  .headline span { display: block; }
  .headline span + span { padding-left: 61px; }

  .service { position: absolute; top: 215px; width: 170px; text-align: center; }
  .service svg { display: block; margin: 0 auto; }
  .service__label {
    margin-top: 16px; font-family: "Alegreya Sans SC", sans-serif; font-weight: 700;
    color: var(--lime); font-size: 19px; letter-spacing: 0.3px;
  }
  .service--tech { left: 251px; }
  .service--staff { left: 416px; }
  .service--domains { left: 583px; }

  .brand {
    position: absolute; left: 874px; top: 34px; width: 310px; color: var(--white);
  }
  .brand__name {
    display: flex; align-items: center; gap: 10px;
    font-family: "Lato", sans-serif; font-weight: 400; font-size: 25px; line-height: 32px;
    white-space: nowrap;
  }
  .brand__mark { width: 14px; height: 14px; background: var(--white); flex: none; }
  .brand__tag { margin-top: 8px; padding-left: 24px; font-size: 13px; letter-spacing: 0.2px; white-space: nowrap; }

  .contact { position: absolute; left: 808px; list-style: none; color: var(--white); font-size: 18px; }
  .contact li { position: absolute; left: 0; display: flex; align-items: center; white-space: nowrap; }
  .contact svg { width: 28px; height: 28px; margin-right: 12px; flex: none; }
  .contact__phone { top: 236px; }
  .contact__mail { top: 291px; }
  .contact__web { top: 346px; }

  .avatar {
    position: absolute; left: 32px; top: 437px; width: 190px; height: 190px;
    background: var(--white); border: 1px solid var(--frame-grey); padding: 7px;
  }
  .avatar__inner {
    width: 100%; height: 100%; background: var(--lime);
    display: flex; align-items: center; justify-content: center; text-align: center;
    font-family: "Lato", sans-serif; font-weight: 400; color: var(--white); font-size: 22px; line-height: 32px;
  }
</style>
</head>
<body>
  <section class="cover" aria-label="Page cover">
    <svg class="cover__panel" width="1200" height="440" viewBox="0 0 1200 440">
      <polygon points="854,0 1200,0 1200,440 819,440" fill="var(--lime)"/>
    </svg>

    <h1 class="headline">
      <span>Find out how Lanternfold Can Provide</span>
      <span>Customized Solution For Your IT needs</span>
    </h1>

    <div class="service service--tech">
      <svg width="112" height="112" viewBox="0 0 112 112" fill="none" stroke="var(--lime)" stroke-width="3">
        <circle cx="56" cy="56" r="54"/>
        <circle cx="54" cy="58" r="24" stroke-width="6"/>
        <circle cx="54" cy="58" r="13" stroke-width="5"/>
        <circle cx="54" cy="58" r="4" fill="var(--lime)"/>
        <line x1="54" y1="58" x2="80" y2="32" stroke-width="4"/>
        <polyline points="72,30 82,30 82,40" stroke-width="4"/>
      </svg>
      <div class="service__label">Technology</div>
    </div>

    <div class="service service--staff">
      <svg width="112" height="112" viewBox="0 0 112 112" fill="none" stroke="var(--lime)" stroke-width="3">
        <circle cx="56" cy="56" r="54"/>
        <circle cx="44" cy="44" r="10" stroke-width="4"/>
        <circle cx="44" cy="44" r="15" stroke-width="3" stroke-dasharray="5 4"/>
        <circle cx="62" cy="34" r="6" stroke-width="3"/>
        <rect x="48" y="54" width="32" height="20" rx="2" stroke-width="4"/>
        <line x1="40" y1="80" x2="88" y2="80" stroke-width="4"/>
      </svg>
      <div class="service__label">IT Staffing</div>
    </div>

    <div class="service service--domains">
      <svg width="112" height="112" viewBox="0 0 112 112" fill="none" stroke="var(--lime)" stroke-width="3">
        <circle cx="56" cy="56" r="54"/>
        <circle cx="56" cy="56" r="28" stroke-width="5"/>
        <ellipse cx="56" cy="56" rx="12" ry="28" stroke-width="3"/>
        <line x1="28" y1="56" x2="84" y2="56" stroke-width="3"/>
        <rect x="30" y="48" width="52" height="16" fill="var(--lime)" stroke="none"/>
        <text x="56" y="61" text-anchor="middle" font-family="Lato, sans-serif" font-size="13" font-weight="700" fill="var(--white)" stroke="none">www</text>
      </svg>
      <div class="service__label">IT Domians</div>
    </div>

    <div class="brand">
      <div class="brand__name"><span class="brand__mark"></span>Lanternfold Tech Systems</div>
      <div class="brand__tag">Enterprise Apps, Staffing and IT Consulting</div>
    </div>

    <ul class="contact">
      <li class="contact__phone">
        <svg viewBox="0 0 28 28" fill="none" stroke="var(--white)" stroke-width="1.6">
          <rect x="8" y="2" width="12" height="24" rx="2"/>
          <line x1="8" y1="6" x2="20" y2="6"/><line x1="8" y1="21" x2="20" y2="21"/>
        </svg>
        1(800)555-0147
      </li>
      <li class="contact__mail">
        <svg viewBox="0 0 28 28" fill="none" stroke="var(--white)" stroke-width="1.6">
          <rect x="2" y="7" width="24" height="15" transform="rotate(-10 14 14)"/>
          <polyline points="2,9 14,17 26,5" transform="rotate(-4 14 14)"/>
        </svg>
        contact@lanternfoldsystems.example
      </li>
      <li class="contact__web">
        <svg viewBox="0 0 28 28">
          <circle cx="14" cy="14" r="12" fill="var(--white)"/>
          <path d="M9 8c3 0 4 3 2 5s1 4-1 6M18 6c-1 3 2 4 4 4M17 18c2-1 4 0 5 2" stroke="var(--lime)" stroke-width="2" fill="none"/>
        </svg>
        http://www.lanternfoldsystems.example
      </li>
    </ul>
  </section>

  <div class="avatar" aria-label="Profile picture">
    <div class="avatar__inner">Lanternfold<br>Systems</div>
  </div>
</body>
</html>
```